A website for a Maltese Law Firm

Our law firm needs a website to further its business. The site should have a simple yet effective design. We would need the following sections: About us, Practice Areas, About Malta, Contact. These should be further split as follows:

About us: Our firm, Our values, What others say, Offices

Practice Areas: Crimimal, Citizenship & Residence, Sovereign Patron Pathway, Criminal Defence, Civil Litigation, Arbitration and ADR, Commercial and Corporate, Media Law.

About Malta: just one section.

Contact: Just one section

We would also need a news feed at the front of the site to include latest news regarding our cases.

At the bottom we need a section for our Terms and a Privacy Statement.

Our logo is being attached.

Target Market(s)

All clients looking for legal assistance in Malta

Industry/Entity Type

Legal

Coding

Coded - Design and coding required

Number of Pages Required

1 page

Requirements
Must have
• It must be simple yet striking.

```html
<!DOCTYPE html>
<html lang="en">
<head>
<meta charset="utf-8">
<title>Vellacott &amp; Serran Advocates</title>
<link href="https://fonts.googleapis.com/css2?family=Cinzel:wght@400;600&family=Arimo:wght@400;700&display=swap" rel="stylesheet">
<style>
:root{
  --orange:#f0a04b;
  --orange-deep:#e8913a;
  --title:#e8943a;
  --ink:#333;
  --muted:#777;
  --tile:rgba(95,95,95,.75);
  --footer-top:#c46f27;
  --footer-bottom:#d99443;
  --footer-bar:#c97a2f;
  --white:#fff;
}
*{box-sizing:border-box;margin:0;padding:0}
html,body{width:1200px;height:2612px;overflow:hidden}
body{position:relative;font-family:"Arimo",Arial,sans-serif;color:var(--ink);background:var(--white)}
a{color:inherit;text-decoration:none}

.topbar{position:absolute;left:99px;top:0;width:1002px;height:33px;background:var(--orange);
  clip-path:polygon(0 0,100% 0,97% 100%,3% 100%);color:var(--white);font-size:12px;
  display:flex;align-items:center;padding:0 60px}
.topbar .greeting{flex:1}
.topbar .contact{display:flex;gap:36px}
.topbar .contact span{display:flex;align-items:center;gap:8px}

.header{position:absolute;left:0;top:33px;width:1200px;height:79px;display:flex;align-items:center;padding:0 99px}
.brand{font-family:"Arimo",Arial,sans-serif;font-weight:700;font-size:18px;color:#222;flex:1;line-height:1}
.nav{display:flex;gap:52px;font-size:13px;color:#555;align-items:center}
.nav .active{color:var(--orange)}

.hero{position:absolute;left:0;top:112px;width:1200px;height:522px;
  background:linear-gradient(100deg,#8a7a66 0%,#5a5148 35%,#3d3a38 55%,#9a8c7e 80%,#6b5f55 100%)}
.hero-title{position:absolute;left:606px;top:188px;font-family:"Cinzel",serif;color:var(--white);line-height:1.1}
.hero-title .l1{font-size:54px}
.hero-title .l2{font-size:40px}
.hero .arrow{position:absolute;top:250px}

.features{position:absolute;left:99px;top:585px;width:1002px;height:96px;display:flex}
.feature{flex:1;display:flex;align-items:center;justify-content:center;gap:18px;color:var(--white);font-size:22px;background:var(--orange)}
.feature.mid{background:var(--orange-deep)}

.welcome{position:absolute;left:0;top:728px;width:1200px;text-align:center}
.section-title{font-family:"Cinzel",serif;font-weight:400;color:var(--title);font-size:28px;letter-spacing:1px}
.welcome p{width:770px;margin:22px auto 0;font-size:11px;line-height:19px;color:var(--muted)}
.callrow{display:flex;justify-content:center;align-items:center;gap:36px;margin-top:30px;font-size:16px;color:#444}
.pill{background:var(--orange);color:var(--white);border-radius:24px;padding:12px 30px;font-size:17px}

.practice{position:absolute;left:0;top:968px;width:1200px;height:554px;background:linear-gradient(180deg,#262626,#3a3a3a 50%,#222)}
.practice .section-title{text-align:center;margin-top:48px}
.practice p{width:690px;margin:14px auto 0;text-align:center;color:#eee;font-size:12px;line-height:20px}
.grid{position:absolute;left:99px;top:161px;width:1002px;display:grid;grid-template-columns:repeat(4,234px);column-gap:22px;row-gap:21px}
.tile{height:160px;background:var(--tile);display:flex;flex-direction:column;align-items:center;justify-content:center;gap:18px;color:var(--white);font-size:16px}

.news{position:absolute;left:0;top:1568px;width:1200px}
.news .section-title{text-align:center}
.cards{position:absolute;left:99px;top:60px;display:flex;gap:40px}
.card{width:309px;height:403px;background:#f5f5f5;border:1px solid #e6e6e6;position:relative}
.card .photo{height:196px}
.avatar{position:absolute;left:24px;top:164px;width:62px;height:62px;border-radius:50%;background:#c8b8a4;border:3px solid var(--white)}
.card .date{position:absolute;left:100px;top:206px;font-size:11px;color:#555}
.card h3{position:absolute;left:24px;top:252px;font-size:17px;font-weight:400;color:#222}
.card p{position:absolute;left:24px;top:281px;width:262px;font-size:11px;line-height:18px;color:#555}
.card .more{position:absolute;left:24px;top:358px;font-size:11px;color:#222;text-decoration:underline}

.footer{position:absolute;left:0;top:2085px;width:1200px;height:467px;background:linear-gradient(180deg,var(--footer-top),var(--footer-bottom));color:var(--white)}
.footer .brand{position:absolute;left:0;width:1200px;top:66px;text-align:center;color:var(--white);font-size:24px}
.socials{position:absolute;top:118px;left:0;width:1200px;display:flex;justify-content:center;gap:20px}
.socials span{width:13px;height:13px;border-radius:50%;background:var(--white)}
.col{position:absolute;top:172px;font-size:11px;line-height:21px}
.col h4{font-size:16px;font-weight:400;margin-bottom:10px}
.newsletter input{display:block;width:221px;height:38px;background:#e8b483;border:0;padding:0 12px;font-size:10px;color:var(--white);font-style:italic;font-family:inherit}
.newsletter .send{display:inline-block;margin:14px 0 0 138px;border:2px solid var(--white);border-radius:20px;padding:8px 14px;font-size:11px}
.divider{position:absolute;left:99px;top:327px;width:1002px;height:1px;background:rgba(255,255,255,.25)}
.terms{position:absolute;left:99px;top:362px;width:1002px;font-size:11px;line-height:21px}
.terms h4{font-size:14px;font-weight:400;margin-bottom:8px}
.copyright{position:absolute;left:0;top:2552px;width:1200px;height:60px;background:var(--footer-bar);color:var(--white);font-size:11px;display:flex;align-items:center;justify-content:center}
</style>
</head>
<body>

<div class="topbar">
  <span class="greeting">Welcome To Vellacott &amp; Serran Advocates law firm from Malta</span>
  <div class="contact">
    <span><svg width="11" height="11" viewBox="0 0 24 24"><path fill="#fff" d="M6.6 10.8a15 15 0 0 0 6.6 6.6l2.2-2.2c.3-.3.7-.4 1-.2 1.1.4 2.3.6 3.6.6.6 0 1 .4 1 1V20c0 .6-.4 1-1 1A17 17 0 0 1 3 4c0-.6.4-1 1-1h3.5c.6 0 1 .4 1 1 0 1.3.2 2.5.6 3.6.1.3 0 .7-.2 1z"/></svg>Call us on : + 7400135528</span>
    <span><svg width="12" height="10" viewBox="0 0 24 18"><rect x="1" y="1" width="22" height="16" fill="none" stroke="#fff" stroke-width="2"/><path d="M1 1l11 9 11-9" fill="none" stroke="#fff" stroke-width="2"/></svg>Mail us on : info@vellacottserran.mt</span>
  </div>
</div>

<header class="header">
  <div class="brand">Vellacott &amp; Serran</div>
  <nav class="nav">
    <a class="active" href="#">Home</a><a href="#">About us</a><a href="#">Practice Areas</a><a href="#">About Malta</a><a href="#">Contact us</a>
    <svg width="13" height="13" viewBox="0 0 24 24"><circle cx="10" cy="10" r="7" fill="none" stroke="#555" stroke-width="3"/><path d="M15 15l7 7" stroke="#555" stroke-width="3"/></svg>
  </nav>
</header>

<section class="hero" role="img" aria-label="Team of four lawyers in business suits standing in an office">
  <svg class="arrow" style="left:42px" width="14" height="24" viewBox="0 0 14 24"><path d="M12 2L2 12l10 10" fill="none" stroke="#fff" stroke-width="2"/></svg>
  <svg class="arrow" style="right:42px" width="14" height="24" viewBox="0 0 14 24"><path d="M2 2l10 10L2 22" fill="none" stroke="#fff" stroke-width="2"/></svg>
  <div class="hero-title"><div class="l1">WE ARE</div><div class="l2">VELLACOTT &amp; SERRAN</div></div>
</section>

<div class="features">
  <div class="feature"><svg width="32" height="32" viewBox="0 0 24 24"><rect x="2" y="5" width="15" height="16" rx="2" fill="none" stroke="#fff" stroke-width="2"/><path d="M9 15l1-4 9-9 3 3-9 9z" fill="#fff"/></svg>Request A Quote</div>
  <div class="feature mid"><svg width="32" height="32" viewBox="0 0 24 24"><circle cx="10" cy="10" r="7" fill="none" stroke="#fff" stroke-width="3"/><path d="M15 15l7 7" stroke="#fff" stroke-width="3.5"/></svg>Investigation</div>
  <div class="feature"><svg width="28" height="32" viewBox="0 0 24 28"><circle cx="12" cy="7" r="6" fill="#fff"/><path d="M1 27c0-8 5-12 11-12s11 4 11 12z" fill="#fff"/></svg>Legal Proceeding</div>
</div>

<section class="welcome">
  <h2 class="section-title">WELCOME TO VELLACOTT &amp; SERRAN</h2>
  <p>It is a long established fact that a reader will be distracted by the readable content of a page when looking at its layout. The point of using Lorem Ipsum is that it has a more-or-less normal distribution of letters, as opposed to using 'Content here, content here', making it look like readable English. Many desktop publishing packages and web page editors now use Lorem Ipsum as their default model text, and a search for 'lorem ipsum' will uncover</p>
  <div class="callrow"><span>Call For A FREE Consultation!</span><span class="pill">(880) - 7400135528</span><span>Available for 24/7</span></div>
</section>

<section class="practice">
  <h2 class="section-title">AREAS OF PRACTICE</h2>
  <p>Sed ut perspiciatis unde omnis iste natus error sit voluptatem accusantium doloremque laudantium, totam rem aperiam, eaque ipsa quae ab illo inventore veritatis et quasi architecto beatae vitae dicta sunt explicabo</p>
  <div class="grid">
    <div class="tile"><svg width="42" height="42" viewBox="0 0 42 42"><circle cx="13" cy="27" r="9" fill="none" stroke="#fff" stroke-width="4"/><circle cx="29" cy="15" r="9" fill="none" stroke="#fff" stroke-width="4"/></svg>Crimimal</div>
    <div class="tile"><svg width="40" height="42" viewBox="0 0 40 42"><circle cx="20" cy="11" r="9" fill="#fff"/><path d="M3 40c0-12 7-17 17-17s17 5 17 17z" fill="#fff"/></svg>Citizenship&amp;Residence</div>
    <div class="tile"><svg width="40" height="42" viewBox="0 0 40 42"><circle cx="23" cy="16" r="12" fill="none" stroke="#fff" stroke-width="4"/><path d="M14 25L3 37" stroke="#fff" stroke-width="5"/><circle cx="23" cy="14" r="4" fill="#fff"/></svg>Sovereign Patron Pathway</div>
    <div class="tile"><svg width="36" height="42" viewBox="0 0 36 42"><path d="M18 2l16 6v12c0 10-7 17-16 20C9 37 2 30 2 20V8z" fill="#fff"/></svg>Criminal Defence</div>
    <div class="tile"><svg width="42" height="40" viewBox="0 0 42 40"><rect x="4" y="2" width="34" height="7" fill="#fff"/><rect x="9" y="11" width="6" height="20" fill="#fff"/><rect x="18" y="11" width="6" height="20" fill="#fff"/><rect x="27" y="11" width="6" height="20" fill="#fff"/><rect x="2" y="33" width="38" height="6" fill="#fff"/></svg>Civil Litigation</div>
    <div class="tile"><svg width="44" height="40" viewBox="0 0 44 40"><path d="M22 3l19 34H3z" fill="none" stroke="#fff" stroke-width="4"/><circle cx="22" cy="25" r="5" fill="#fff"/></svg>Arbitration &amp; ADR</div>
    <div class="tile"><svg width="20" height="44" viewBox="0 0 20 44"><path d="M6 2h8l-2 6H8z" fill="#fff"/><path d="M8 10h4l4 24-6 8-6-8z" fill="#fff"/></svg>Commercial &amp; Corporate</div>
    <div class="tile"><svg width="44" height="40" viewBox="0 0 44 40"><path d="M22 24c-9-6-13-10-13-15a6 6 0 0 1 13-2 6 6 0 0 1 13 2c0 5-4 9-13 15z" fill="#fff"/><path d="M2 22l8 12h24l8-12" fill="none" stroke="#fff" stroke-width="4"/></svg>Media Law</div>
  </div>
</section>

<section class="news">
  <h2 class="section-title">LATEST NEWS</h2>
  <div class="cards">
    <article class="card">
      <div class="photo" role="img" aria-label="Brass scales of justice with toy cars on a desk" style="background:linear-gradient(135deg,#d9b07a,#a8733d)"></div>
      <div class="avatar" role="img" aria-label="Author portrait"></div>
      <span class="date">Posted On June 2016</span>
      <h3>NEQUE PORRO QUISQUAM</h3>
      <p>There are many variations of passages of Lorem Ipsum available, but the majority have suffered alteration in some form, by injected humour, or randomised ...</p>
      <a class="more" href="#">Read More</a>
    </article>
    <article class="card">
      <div class="photo" role="img" aria-label="Hands in handcuffs against a dark background" style="background:linear-gradient(135deg,#3a3532,#0e0e0e)"></div>
      <div class="avatar" role="img" aria-label="Author portrait" style="background:#d8c2a0"></div>
      <span class="date">Posted On June 2016</span>
      <h3>NEQUE PORRO QUISQUAM</h3>
      <p>There are many variations of passages of Lorem Ipsum available, but the majority have suffered alteration in some form, by injected humour, or randomised ...</p>
      <a class="more" href="#">Read More</a>
    </article>
    <article class="card">
      <div class="photo" role="img" aria-label="Medical staff meeting around a table" style="background:linear-gradient(135deg,#f2f2f2,#bcc4c8)"></div>
      <div class="avatar" role="img" aria-label="Author portrait" style="background:#b9a590"></div>
      <span class="date">Posted On June 2016</span>
      <h3>NEQUE PORRO QUISQUAM</h3>
      <p>There are many variations of passages of Lorem Ipsum available, but the majority have suffered alteration in some form, by injected humour, or randomised ...</p>
      <a class="more" href="#">Read More</a>
    </article>
  </div>
</section>

<footer class="footer">
  <div class="brand">Vellacott &amp; Serran</div>
  <div class="socials"><span></span><span></span><span></span><span></span><span></span></div>
  <div class="col" style="left:99px"><h4>COMPANY</h4>About us<br>Services<br>Blog<br>News</div>
  <div class="col" style="left:253px"><h4>COMMUNITY</h4>Guiglines<br>Terms and conditions<br>privacy policy<br>site map</div>
  <div class="col" style="left:449px"><h4>FOLLOW US</h4>Friendbook<br>Chirper<br>Snapgram<br>Searchly</div>
  <div class="col" style="left:625px"><h4>CONTACT US</h4>Address : 200 Latin words,<br>combined with a handful | 852.789<br>Ph : (088)-740013552<br>Fax : (088)-740013560</div>
  <div class="col newsletter" style="left:880px"><h4>NEWSLETTER</h4><input type="text" placeholder="Enter The mail id"><span class="send">Send Now</span></div>
  <div class="divider"></div>
  <div class="terms"><h4>Terms and a Privacy</h4>It is a long established fact that a reader will be distracted by the readable content of a page when looking at its layout. The point of using Lorem Ipsum is that it has a more-or-less normal distribution of letters, as opposed to using 'Content here, content here', making it look like readable English. Many desktop publishing packages and web page editors now</div>
</footer>
<div class="copyright">Copyrights@2016Company name all rights reserved</div>

</body>
</html>
```